Business Card Design for Software Development Company

I am looking for a business card design the incorporates my new logo (attached below).

Key information to include:
Name: Martin Quelbrook
Title: CEO
Email: martin@brightwellcivic.example
Phone: 555-218-9403
Website: www.brightwellcivic.example

NOTE: This design should be easy to edit so that we can order cards for different members of our team.

```html
<!DOCTYPE html>
<html lang="en">
<head>
<meta charset="utf-8">
<title>Brightwell Civic Business Card</title>
<link rel="stylesheet" href="https://fonts.googleapis.com/css2?family=Montserrat:wght@400&family=Raleway:wght@700&display=swap">
<style>
  :root {
    --stage: #2f2f31;
    --navy: #394259;
    --ink: #343b52;
    --white: #ffffff;
  }
  * { box-sizing: border-box; margin: 0; padding: 0; }
  html, body { width: 1200px; height: 1059px; overflow: hidden; }
  body { background: var(--stage); position: relative; font-family: "Montserrat", sans-serif; }

  .card {
    position: absolute;
    left: 256px;
    width: 688px;
    height: 391px;
    box-shadow: 0 14px 26px rgba(0,0,0,0.55);
  }
  .card--front { top: 100px; background: var(--white); }
  .card--back { top: 537px; background: var(--navy); }

  .brand-name {
    font-family: "Raleway", sans-serif;
    font-weight: 700;
    text-transform: uppercase;
    letter-spacing: 3px;
    line-height: 1;
    white-space: nowrap;
  }
  .card--front .brand-name {
    position: absolute;
    right: 39px;
    top: 60px;
    font-size: 30px;
    color: var(--ink);
  }
  .card--back .brand-name {
    position: absolute;
    left: 50%;
    top: 50%;
    transform: translate(-50%, -60%);
    font-size: 40px;
    color: var(--white);
  }

  .name-bar {
    position: absolute;
    left: 0;
    top: 219px;
    width: 15px;
    height: 42px;
    background: var(--ink);
  }
  .person { position: absolute; left: 28px; top: 217px; color: var(--ink); }
  .person__name {
    font-family: "Raleway", sans-serif;
    font-weight: 700;
    font-size: 26px;
    line-height: 1;
    text-transform: uppercase;
  }
  .person__title { font-size: 19px; line-height: 1.25; }

  .contacts { position: absolute; left: 28px; top: 288px; list-style: none; color: var(--ink); }
  .contacts li {
    display: flex;
    align-items: center;
    gap: 8px;
    height: 26px;
    font-size: 17px;
    letter-spacing: 0.3px;
  }
  .contacts svg { width: 13px; height: 13px; fill: var(--ink); flex: none; }
</style>
</head>
<body>
  <section class="card card--front">
    <div class="brand-name">Brightwell Civic</div>
    <div class="name-bar"></div>
    <div class="person">
      <h1 class="person__name">Martin Quelbrook</h1>
      <p class="person__title">CEO</p>
    </div>
    <ul class="contacts">
      <li>
        <svg viewBox="0 0 16 16" aria-hidden="true"><path d="M3.6 1.2l2.3 2.6-1.3 1.6c.9 2 2.3 3.5 4.4 4.6l1.6-1.3 2.6 2.3-1.6 2.3C7 13 2.6 8.6 1.2 2.9z"/></svg>
        555-218-9403
      </li>
      <li>
        <svg viewBox="0 0 16 16" aria-hidden="true"><path d="M1 3h14v1.2L8 9 1 4.2z M1 6l7 4.6L15 6v7H1z"/></svg>
        martin@brightwellcivic.example
      </li>
      <li>
        <svg viewBox="0 0 16 16" aria-hidden="true"><circle cx="8" cy="8" r="6.8" fill="none" stroke="#343b52" stroke-width="1.3"/><ellipse cx="8" cy="8" rx="3" ry="6.8" fill="none" stroke="#343b52" stroke-width="1.1"/><path d="M1.2 8h13.6M2.3 4.8h11.4M2.3 11.2h11.4" stroke="#343b52" stroke-width="1.1"/></svg>
        www.brightwellcivic.example
      </li>
    </ul>
  </section>

  <section class="card card--back">
    <div class="brand-name">Brightwell Civic</div>
  </section>
</body>
</html>
```